Birchline Septic Solutions

Would like to see some single sided ones but would also like to see some double sided with one sided only being the logo. Owners name is Colin Vandro. Phone number is 555-214-0387
Services are pumping, inspections, installs, and repairs

Contact Information for Business Card

555-241-0387 Colin Vandro Ashford Ridge, OH

```html
<!DOCTYPE html>
<html lang="en">
<head>
<meta charset="utf-8">
<title>Birchline Septic Solutions – Business Cards</title>
<link href="https://fonts.googleapis.com/css2?family=Montserrat:wght@400;500;700;800&display=swap" rel="stylesheet">
<style>
  :root {
    --backdrop: #e4e4e4;
    --card-black: #000000;
    --card-white: #ffffff;
    --teal: #06b6b0;
    --teal-soft: #2fbdb6;
    --text-light: #ffffff;
    --text-dark: #141414;
  }
  html, body {
    margin: 0;
    padding: 0;
    width: 1200px;
    height: 856px;
    overflow: hidden;
    background: var(--backdrop);
    font-family: "Montserrat", Arial, sans-serif;
  }
  .canvas {
    position: relative;
    width: 1200px;
    height: 856px;
  }
  .card {
    position: absolute;
    top: 273px;
    width: 540px;
    height: 309px;
    overflow: hidden;
    box-shadow: 0 10px 28px rgba(0,0,0,0.28);
  }
  .card--front { left: 40px; background: var(--card-white); }
  .card--back  { left: 620px; background: var(--card-black); }

  .swoosh {
    position: absolute;
    inset: 0;
    width: 540px;
    height: 309px;
  }

  .brand-name {
    position: absolute;
    font-weight: 800;
    text-transform: uppercase;
    text-align: center;
    line-height: 1;
    margin: 0;
  }
  .brand-name__main { display: block; letter-spacing: 0.02em; }
  .brand-name__sub  { display: block; letter-spacing: 0.32em; margin-top: 8px; }

  .card--front .brand-name {
    left: 22px;
    top: 108px;
    width: 250px;
    color: var(--text-dark);
  }
  .card--front .brand-name__main { font-size: 38px; }
  .card--front .brand-name__sub  { font-size: 11px; }

  .contact {
    position: absolute;
    right: 26px;
    top: 60px;
    text-align: right;
    color: var(--text-light);
  }
  .contact__name {
    margin: 0;
    font-size: 17px;
    font-weight: 700;
    color: var(--teal);
    text-transform: uppercase;
  }
  .contact__role {
    margin: 2px 0 22px;
    font-size: 12px;
    font-weight: 400;
  }
  .contact__line {
    margin: 0;
    font-size: 12px;
    line-height: 1.55;
    font-weight: 400;
  }
  .contact__icon {
    width: 11px;
    height: 11px;
    vertical-align: -1px;
    margin-left: 4px;
  }

  .card--back .brand-name {
    left: 0;
    right: 0;
    top: 72px;
    color: var(--text-light);
  }
  .card--back .brand-name__main { font-size: 52px; }
  .card--back .brand-name__sub  { font-size: 14px; margin-top: 12px; }

  .services {
    position: absolute;
    left: 0;
    right: 0;
    top: 196px;
    text-align: center;
    color: var(--text-light);
    font-size: 15px;
    font-weight: 500;
    line-height: 1.6;
    margin: 0;
  }
  .services__tick {
    width: 12px;
    height: 12px;
    vertical-align: -1px;
    margin: 0 5px 0 8px;
  }
</style>
</head>
<body>
<main class="canvas">

  <section class="card card--front" aria-label="Business card front">
    <svg class="swoosh" viewBox="0 0 540 309" aria-hidden="true">
      <path d="M352,0 L540,0 L540,309 L150,309 C240,285 282,230 300,160 C318,90 318,35 352,0 Z" fill="var(--card-black)"/>
      <path d="M340,0 C306,35 306,90 288,160 C270,230 228,282 120,309" fill="none" stroke="var(--teal)" stroke-width="9"/>
      <path d="M327,0 C293,35 293,90 275,160 C257,228 215,278 96,309" fill="none" stroke="var(--card-black)" stroke-width="3"/>
    </svg>

    <h1 class="brand-name">
      <span class="brand-name__main">Birchline</span>
      <span class="brand-name__sub">Septic Solutions</span>
    </h1>

    <div class="contact">
      <p class="contact__name">Colin Vandro</p>
      <p class="contact__role">Owners</p>
      <p class="contact__line">555-214-0387
        <svg class="contact__icon" viewBox="0 0 24 24" aria-hidden="true"><path fill="var(--teal)" d="M6.6 10.8a15.1 15.1 0 0 0 6.6 6.6l2.2-2.2a1 1 0 0 1 1-.25 11.4 11.4 0 0 0 3.6.57 1 1 0 0 1 1 1V20a1 1 0 0 1-1 1A17 17 0 0 1 3 4a1 1 0 0 1 1-1h3.5a1 1 0 0 1 1 1c0 1.25.2 2.45.57 3.57a1 1 0 0 1-.25 1Z"/></svg>
      </p>
      <p class="contact__line">555-241-0387 Colin</p>
      <p class="contact__line">Vandro Ashford Ridge, OH</p>
    </div>
  </section>

  <section class="card card--back" aria-label="Business card back">
    <h2 class="brand-name">
      <span class="brand-name__main">Birchline</span>
      <span class="brand-name__sub">Septic Solutions</span>
    </h2>

    <p class="services">
      <svg class="services__tick" viewBox="0 0 24 24" aria-hidden="true"><circle cx="12" cy="12" r="10" fill="none" stroke="var(--text-light)" stroke-width="2.5"/><path d="M7 12.5l3.3 3.3L17 9" fill="none" stroke="var(--text-light)" stroke-width="2.8"/></svg>Services are pumping<br>
      <svg class="services__tick" viewBox="0 0 24 24" aria-hidden="true"><circle cx="12" cy="12" r="10" fill="none" stroke="var(--text-light)" stroke-width="2.5"/><path d="M7 12.5l3.3 3.3L17 9" fill="none" stroke="var(--text-light)" stroke-width="2.8"/></svg>inspections
      <svg class="services__tick" viewBox="0 0 24 24" aria-hidden="true"><circle cx="12" cy="12" r="10" fill="none" stroke="var(--text-light)" stroke-width="2.5"/><path d="M7 12.5l3.3 3.3L17 9" fill="none" stroke="var(--text-light)" stroke-width="2.8"/></svg>installs
      <svg class="services__tick" viewBox="0 0 24 24" aria-hidden="true"><circle cx="12" cy="12" r="10" fill="none" stroke="var(--text-light)" stroke-width="2.5"/><path d="M7 12.5l3.3 3.3L17 9" fill="none" stroke="var(--text-light)" stroke-width="2.8"/></svg>and repairs
    </p>
  </section>

</main>
</body>
</html>
```